KORVA needs a beautiful/corp web page

We are a pump an compressor repair facility in Alberta Canada. We love clean looks. white yellows greens blues. main page should involve conola fields, sun shine

Reason: i will be guaranteeing the project keep up the good work

Requirements
Must have
• open conola fields

```html
<!DOCTYPE html>
<html lang="en">
<head>
<meta charset="utf-8">
<title>KORVA</title>
<link href="https://fonts.googleapis.com/css2?family=Questrial&family=Open+Sans:wght@400;600;700&display=swap" rel="stylesheet">
<style>
  :root {
    --hero-sky: #9cc4ec;
    --hero-field: #e3d42a;
    --ink: #222222;
    --ink-soft: #555555;
    --band-blue: #0e87b0;
    --band-green: #a5d21f;
    --white: #ffffff;
    --brand-gold: #f0a814;
  }
  * { margin: 0; padding: 0; box-sizing: border-box; }
  html, body { width: 1200px; height: 717px; overflow: hidden; background: var(--white); }
  .page { position: relative; width: 1200px; height: 717px; font-family: "Open Sans", sans-serif; }

  .hero {
    position: absolute; left: 0; top: 0; width: 1200px; height: 583px;
    background: linear-gradient(to bottom, var(--hero-sky) 0%, var(--hero-sky) 35%, var(--hero-field) 65%, var(--hero-field) 100%);
  }

  .site-header {
    position: absolute; left: 0; top: 0; width: 1200px; height: 110px;
    background: rgba(255,255,255,.85);
    border-bottom: 1px solid #8a8a8a;
  }
  .brand {
    position: absolute; left: 104px; top: 44px;
    display: flex; align-items: center; gap: 12px;
  }
  .brand-mark { width: 30px; height: 30px; border-radius: 50%; background: var(--brand-gold); }
  .brand-name {
    font-weight: 700; font-size: 36px; letter-spacing: 1px;
    color: var(--ink); line-height: 1;
  }
  .main-nav {
    position: absolute; left: 620px; top: 65px;
    display: flex; gap: 31px;
    font-size: 15px; letter-spacing: 1.3px; color: var(--ink);
  }

  .headline {
    position: absolute; left: 93px; top: 274px; width: 1014px; height: 57px;
    background: rgba(255,255,255,.55);
    border: 1px solid rgba(255,255,255,.8);
    font-family: "Questrial", sans-serif; font-weight: 400; font-size: 28px; letter-spacing: 3px;
    color: #2a2a2a; text-align: center; line-height: 55px; white-space: nowrap;
  }
  .tagline {
    position: absolute; left: 456px; top: 344px; width: 288px; height: 38px;
    background: rgba(255,255,255,.5);
    border: 1px solid rgba(255,255,255,.75);
    font-family: "Questrial", sans-serif; font-size: 16px; letter-spacing: 1.5px;
    color: #333; text-align: center; line-height: 36px; white-space: nowrap;
  }

  .promo-band { position: absolute; left: 0; top: 583px; width: 1200px; height: 43px; display: flex; }
  .promo-title {
    width: 338px; background: var(--band-blue); color: var(--white);
    font-size: 17px; font-weight: 600; letter-spacing: 1px;
    padding-left: 112px; line-height: 43px; white-space: nowrap;
    text-shadow: 0 1px 2px rgba(0,0,0,.3);
  }
  .promo-text {
    flex: 1; background: var(--band-green); color: var(--white);
    font-size: 15px; font-weight: 600; letter-spacing: .9px;
    padding-left: 39px; line-height: 43px; white-space: nowrap;
    text-shadow: 0 1px 1px rgba(0,0,0,.2);
  }

  .site-footer { position: absolute; left: 0; top: 647px; width: 1200px; text-align: center; font-family: "Questrial", sans-serif; color: var(--ink-soft); }
  .footer-nav { font-size: 14px; letter-spacing: 1.2px; }
  .footer-contact { margin-top: 7px; font-size: 12.5px; letter-spacing: 1.3px; }
  .sep { display: inline-block; margin: 0 13px; }
</style>
</head>
<body>
<div class="page">
  <div class="hero" role="img" aria-label="Photo of an open canola field in yellow bloom under a blue sky"></div>

  <header class="site-header">
    <div class="brand">
      <span class="brand-mark"></span>
      <span class="brand-name">KORVA</span>
    </div>
    <nav class="main-nav">
      <span>HOME</span><span>SOLUTIONS</span><span>PRODUCTS</span><span>ABOUT</span><span>CONTACT</span>
    </nav>
  </header>

  <h1 class="headline">We are a pump an compressor repair facility in Alberta Canada</h1>
  <p class="tagline">Lorem ipsum dolor sit amet</p>

  <section class="promo-band">
    <div class="promo-title">LOREM IPSUM DOLOR</div>
    <div class="promo-text">Lorem ipsum dolor sit amet, consectetur adipisicing elit, sed do eiusmod tempor.</div>
  </section>

  <footer class="site-footer">
    <div class="footer-nav">Home<span class="sep">I</span>Products<span class="sep">I</span>Solutions<span class="sep">I</span>Choose us<span class="sep">I</span>About us<span class="sep">I</span>Contact</div>
    <div class="footer-contact">Your info mail<span class="sep">I</span>Address<span class="sep">I</span>Phone number</div>
  </footer>
</div>
</body>
</html>
```